RVT Business Card Design

We are an independent auto dealer who specializes in commercial & fleet vehicles, we are family owned and operated and have been in business since 2001. We stock late model, low mileage, white trucks & vans. We mostly deal with companies in the construction and service industries. We are just looking to try to freshen up our old business card, we do not want to change the logo at this point, because it is well know within the southwest region & construction community. I have attached our logo and a PDF of our current business card for reference.
Updates
If the address is stacked there is no comma (,) after NE. Everyone keeps putting it in with this format and it is not correct.
482 Morrow Ave NE
Vallecito, NM 87590
If the address is all on one line, then there will be a comma (,) after NE
482 Morrow Ave NE, Vallecito, NM 87590
Please make changes accordingly, thank you for your attention in this matter.
Industry/Entity Type
Construction
Contact Information for Business Card
482 Morrow Ave NE, Vallecito, NM 87590, Dorian Pellew, Vice President, dorian@rvtfleetcars.example, www.RVTfleetcars.example, ph 505-218-4470, fax 505-627-1904, cell 505-763-2085
Look and feel

```html
<!DOCTYPE html>
<html lang="en">
<head>
<meta charset="utf-8">
<title>RVT Auto Sales – Business Card</title>
<link href="https://fonts.googleapis.com/css2?family=Open+Sans:wght@400;600;700&display=swap" rel="stylesheet">
<style>
  :root {
    --page: #ecebea;
    --card-light: #f4f4f4;
    --card-light-edge: #e4e4e4;
    --red: #ee2a30;
    --red-deep: #d8151c;
    --ink: #2e2e2e;
    --ink-soft: #555555;
    --on-red: #ededed;
    --on-red-strong: #3a3a3a;
  }
  * { box-sizing: border-box; margin: 0; padding: 0; }
  html, body {
    width: 1200px; height: 900px; overflow: hidden;
    background: var(--page);
    font-family: "Open Sans", Arial, sans-serif;
  }
  .canvas {
    width: 1200px; height: 900px;
    display: flex; align-items: center; justify-content: center;
  }
  .business-card {
    width: 840px; height: 480px;
    display: flex;
    box-shadow: 0 10px 30px rgba(0,0,0,0.18);
  }
  .brand-side {
    width: 370px;
    background: linear-gradient(160deg, var(--card-light), var(--card-light-edge));
    padding: 48px 26px 40px 34px;
    display: flex; flex-direction: column; justify-content: space-between;
  }
  .company-mark {
    display: flex; align-items: center; gap: 12px;
    white-space: nowrap;
  }
  .company-mark__square {
    flex: none;
    width: 20px; height: 20px; background: var(--ink);
  }
  .company-mark__name {
    font-size: 33px; font-weight: 700; color: var(--ink);
    line-height: 1;
  }
  .company-tagline {
    margin-top: 16px; margin-left: 32px;
    font-size: 15px; font-weight: 400; color: var(--ink-soft);
    line-height: 1.4;
  }
  .online-contact {
    font-size: 21px; font-weight: 600; color: var(--ink);
    line-height: 1.45;
    white-space: nowrap;
  }
  .detail-side {
    flex: 1;
    background: linear-gradient(150deg, var(--red), var(--red-deep));
    padding: 46px 36px 40px 44px;
    display: flex; flex-direction: column;
  }
  .person-name {
    font-size: 36px; font-weight: 700; color: var(--on-red-strong);
    line-height: 1.15;
  }
  .person-title {
    font-size: 32px; font-weight: 400; color: var(--on-red);
    line-height: 1.2; margin-top: 2px;
  }
  .address {
    margin-top: 56px;
    font-size: 24px; font-weight: 600; color: var(--on-red);
    line-height: 1.3; font-style: normal;
  }
  .phone-list {
    margin-top: 16px;
    display: grid;
    grid-template-columns: 100px 26px auto;
    row-gap: 2px;
    font-size: 24px; font-weight: 600; color: var(--on-red);
    line-height: 1.3;
  }
</style>
</head>
<body>
<main class="canvas">
  <article class="business-card">
    <section class="brand-side">
      <div class="brand-block">
        <div class="company-mark">
          <span class="company-mark__square"></span>
          <span class="company-mark__name">RVT Auto Sales</span>
        </div>
        <p class="company-tagline">Specializing in Commercial<br>&amp; Fleet Vehicles</p>
      </div>
      <div class="online-contact">
        <p>www.RVTfleetcars.example</p>
        <p>dorian@rvtfleetcars.example</p>
      </div>
    </section>
    <section class="detail-side">
      <h1 class="person-name">Dorian Pellew</h1>
      <p class="person-title">Vice President</p>
      <address class="address">
        482 Morrow Ave NE<br>
        Vallecito, NM 87590
      </address>
      <div class="phone-list">
        <span>Phone</span><span>:</span><span>505-218-4470</span>
        <span>Cell</span><span>:</span><span>505-763-2085</span>
        <span>Fax</span><span>:</span><span>505-627-1904</span>
      </div>
    </section>
  </article>
</main>
</body>
</html>
```